Halvorsen Construction Needs a Business Card

Our current business card is very bland, and since we have a new logo, we would like a new business card design to reflect our company. It can be a single-sided or two-sided card, but it is important that our contact information appears on the same side. I am attaching a copy of our old card and our new logo. If you need the logo in another format than the one I'm sending, please let me know. This is the information that we must have on our card, but not necessarily in any specific order:
1) Our logo
2) General Contractor
3) Derek Halvorsen, Owner
4) 482 Commerce Ridge Road, Ashford Glen, Ohio 44021
5) Office: 555-384-7150
7) Fax: 555-384-7151
8) Cell: 555-619-7150
9) halvorsenconstruction@qrm.net
10) halvorsenconstruction.com (can be omitted if necessary)
Also, I will need files in a format that I can alter if any of the above information changes in the near future. Thank you in advance for your submissions!
Target Market(s)
Commercial and residential clients, architects, and subcontractors.
Industry/Entity Type
Business

```html
<!DOCTYPE html>
<html lang="en">
<head>
<meta charset="utf-8">
<title>Halvorsen Construction – Business Card</title>
<link rel="stylesheet" href="https://fonts.googleapis.com/css2?family=Open+Sans:wght@400;600;700&display=swap">
<style>
  :root {
    --canvas: #f1f0ed;
    --card-blue: #4a86ae;
    --card-white: #ffffff;
    --tick-white: #ffffff;
    --ink-dark: #1e1e1e;
    --text-blue: #4d7ea6;
    --label-gold: #d3a32b;
    --shadow: rgba(0, 0, 0, 0.18);
  }
  * { box-sizing: border-box; margin: 0; padding: 0; }
  html, body {
    width: 1200px;
    height: 450px;
    overflow: hidden;
    background: var(--canvas);
    font-family: "Open Sans", Arial, sans-serif;
  }
  .stage {
    position: relative;
    width: 1200px;
    height: 450px;
  }
  .card {
    position: absolute;
    top: 82px;
    width: 500px;
    height: 286px;
    box-shadow: 0 6px 18px var(--shadow);
    overflow: hidden;
  }
  .card--front { left: 80px; background: var(--card-blue); }
  .card--back  { left: 620px; background: var(--card-white); }
  .card svg { position: absolute; inset: 0; }

  /* front */
  .ruler-label { font-family: "Open Sans", Arial, sans-serif; font-weight: 600; }
  .front-wordmark {
    position: absolute;
    left: 0; right: 0; top: 128px;
    display: flex;
    align-items: center;
    justify-content: center;
    gap: 12px;
  }
  .wordmark-square {
    width: 36px; height: 36px;
    background: var(--ink-dark);
  }
  .wordmark-name {
    font-weight: 700;
    font-size: 23px;
    letter-spacing: 1px;
    color: var(--ink-dark);
    text-transform: uppercase;
  }

  /* back */
  .back-brand {
    position: absolute;
    left: 38px; top: 34px;
  }
  .back-brand__row { display: flex; align-items: center; gap: 8px; }
  .back-brand .wordmark-square { width: 26px; height: 26px; }
  .back-brand .wordmark-name { font-size: 15px; letter-spacing: 0.5px; }
  .back-brand__tagline {
    margin-top: 2px;
    text-align: right;
    font-size: 7.5px;
    font-weight: 700;
    letter-spacing: 0.6px;
    color: var(--ink-dark);
  }
  .owner {
    position: absolute;
    left: 40px; top: 142px;
    color: var(--text-blue);
    text-align: center;
    font-size: 13px;
    line-height: 1.2;
  }
  .owner__title { font-size: 11.5px; }
  .contact {
    position: absolute;
    left: 168px; top: 108px;
    display: grid;
    grid-template-columns: 52px auto;
    column-gap: 10px;
    row-gap: 1px;
    font-size: 10.5px;
    line-height: 13px;
  }
  .contact dt { color: var(--label-gold); text-align: right; }
  .contact dd { color: var(--text-blue); }
  .contact dd.address { margin-bottom: 2px; }
</style>
</head>
<body>
<main class="stage">

  <section class="card card--front" aria-label="Card front">
    <svg width="500" height="286" viewBox="0 0 500 286">
      <defs>
        <pattern id="inch-eighth" x="39.25" y="0" width="17.5" height="10" patternUnits="userSpaceOnUse"><rect width="1.5" height="10" fill="#fff"/></pattern>
        <pattern id="inch-quarter" x="39.25" y="0" width="35" height="15" patternUnits="userSpaceOnUse"><rect width="1.5" height="15" fill="#fff"/></pattern>
        <pattern id="inch-half" x="39.25" y="0" width="70" height="21" patternUnits="userSpaceOnUse"><rect width="1.5" height="21" fill="#fff"/></pattern>
        <pattern id="inch-whole" x="39.25" y="0" width="140" height="30" patternUnits="userSpaceOnUse"><rect width="1.5" height="30" fill="#fff"/></pattern>
        <pattern id="cm-mm" x="39.25" y="277" width="5.5125" height="9" patternUnits="userSpaceOnUse"><rect width="1.2" height="9" fill="#fff"/></pattern>
        <pattern id="cm-half" x="39.25" y="271" width="27.5625" height="15" patternUnits="userSpaceOnUse"><rect width="1.4" height="15" fill="#fff"/></pattern>
        <pattern id="cm-whole" x="39.25" y="262" width="55.125" height="24" patternUnits="userSpaceOnUse"><rect width="1.5" height="24" fill="#fff"/></pattern>
      </defs>

      <g class="inch-ruler">
        <rect x="39.25" y="0" width="422" height="10" fill="url(#inch-eighth)"/>
        <rect x="39.25" y="0" width="422" height="15" fill="url(#inch-quarter)"/>
        <rect x="39.25" y="0" width="422" height="21" fill="url(#inch-half)"/>
        <rect x="39.25" y="0" width="422" height="30" fill="url(#inch-whole)"/>
        <g class="ruler-label" fill="#fff" font-size="15" text-anchor="middle">
          <text x="40" y="52">0</text>
          <text x="180" y="52">1</text>
          <text x="320" y="52">2</text>
          <text x="460" y="52">3</text>
        </g>
        <text class="ruler-label" x="50" y="52" fill="#fff" font-size="9">INCH</text>
      </g>

      <g class="cm-ruler">
        <rect x="39.25" y="277" width="443" height="9" fill="url(#cm-mm)"/>
        <rect x="39.25" y="271" width="443" height="15" fill="url(#cm-half)"/>
        <rect x="39.25" y="262" width="443" height="24" fill="url(#cm-whole)"/>
        <g class="ruler-label" fill="#fff" font-size="15" text-anchor="middle">
          <text x="40" y="246">0</text>
          <text x="95.1" y="246">1</text>
          <text x="150.3" y="246">2</text>
          <text x="205.4" y="246">3</text>
          <text x="260.5" y="246">4</text>
          <text x="315.6" y="246">5</text>
          <text x="370.8" y="246">6</text>
          <text x="425.9" y="246">7</text>
          <text x="481" y="246">8</text>
        </g>
        <text class="ruler-label" x="50" y="246" fill="#fff" font-size="9">CM</text>
      </g>
    </svg>

    <div class="front-wordmark">
      <span class="wordmark-square" aria-hidden="true"></span>
      <span class="wordmark-name">Halvorsen Construction</span>
    </div>
  </section>

  <section class="card card--back" aria-label="Card back">
    <svg width="500" height="286" viewBox="0 0 500 286">
      <defs>
        <pattern id="back-eighth" x="39.25" y="278" width="17.5" height="8" patternUnits="userSpaceOnUse"><rect width="1.3" height="8" fill="#4d7ea6"/></pattern>
        <pattern id="back-half" x="39.25" y="272" width="70" height="14" patternUnits="userSpaceOnUse"><rect width="1.3" height="14" fill="#4d7ea6"/></pattern>
        <pattern id="back-whole" x="39.25" y="262" width="140" height="24" patternUnits="userSpaceOnUse"><rect width="1.5" height="24" fill="#4d7ea6"/></pattern>
      </defs>
      <g class="inch-ruler">
        <rect x="39.25" y="278" width="422" height="8" fill="url(#back-eighth)"/>
        <rect x="39.25" y="272" width="422" height="14" fill="url(#back-half)"/>
        <rect x="39.25" y="262" width="422" height="24" fill="url(#back-whole)"/>
        <g class="ruler-label" fill="#4d7ea6" font-size="11" text-anchor="middle">
          <text x="40" y="254">0</text>
          <text x="180" y="254">1</text>
          <text x="320" y="254">2</text>
          <text x="460" y="254">3</text>
        </g>
        <text class="ruler-label" x="48" y="254" fill="#4d7ea6" font-size="7">INCH</text>
      </g>
    </svg>

    <div class="back-brand">
      <div class="back-brand__row">
        <span class="wordmark-square" aria-hidden="true"></span>
        <span class="wordmark-name">Halvorsen Construction</span>
      </div>
      <p class="back-brand__tagline">GENERAL CONTRACTOR</p>
    </div>

    <div class="owner">
      <p class="owner__name">Derek Halvorsen</p>
      <p class="owner__title">Owner</p>
    </div>

    <dl class="contact">
      <dt>office</dt><dd>555-384-7150</dd>
      <dt>fax</dt><dd>555-384-7151</dd>
      <dt>cell</dt><dd>555-619-7150</dd>
      <dt>address</dt><dd class="address">482 Commerce Ridge Road, Ashford Glen,<br>Ohio 44021</dd>
      <dt>email</dt><dd>halvorsenconstruction@qrm.net</dd>
      <dt>www</dt><dd>halvorsenconstruction.com</dd>
    </dl>
  </section>

</main>
</body>
</html>
```